stationary deign for trucking company

im a trucking company looking for a professional set of stationary designs i deliver goods from point a to b
Updates

When submitting stationary designs I need envelope design, letterhead, cards, I’d badge etc

Industry/Entity Type

Trucking Company

Requirements
Must have
• must have letter head, business card, envelope, fax sheet, id badge, folder, thank you card, notebook, invoice sheet.
Nice to have
• nice to have them all custom made (letterhead,envelope, business card, I’d badge etc
Should not have
• must not have prepaid sign want i unique design for items

```html
<!DOCTYPE html>
<html lang="en">
<head>
<meta charset="utf-8">
<title>Harlow Freight Lines – Presentation Folder</title>
<link href="https://fonts.googleapis.com/css2?family=Montserrat:wght@400;600&family=Roboto:wght@400;500&display=swap" rel="stylesheet">
<style>
  :root {
    --brand-blue: #0a4f9a;
    --brand-blue-dark: #083f7e;
    --brand-blue-light: #2f6fb3;
    --paper: #f7f7f7;
    --paper-shade: #ececec;
    --ink: #1d1d1f;
    --backdrop: #b9b9b9;
    --white: #ffffff;
  }
  * { box-sizing: border-box; margin: 0; padding: 0; }
  html, body { width: 842px; height: 1200px; overflow: hidden; }
  body {
    background: var(--backdrop);
    font-family: "Roboto", Arial, sans-serif;
    position: relative;
  }
  .spread {
    position: absolute;
    left: 61px;
    width: 720px;
    height: 490px;
    display: flex;
    box-shadow: 0 14px 30px rgba(0,0,0,0.28);
  }
  .spread--outside { top: 45px; }
  .spread--inside { top: 665px; }
  .panel { position: relative; width: 360px; height: 100%; overflow: hidden; }

  /* Outside: back cover */
  .back-cover {
    background: linear-gradient(120deg, var(--brand-blue-light) 0%, var(--brand-blue) 45%, var(--brand-blue-dark) 100%);
    color: var(--white);
  }
  .contact {
    position: absolute;
    left: 30px;
    bottom: 30px;
    font-size: 8.5px;
    line-height: 1.45;
    opacity: 0.9;
  }
  .contact__address { margin-bottom: 8px; }
  .contact__row { display: flex; align-items: center; gap: 5px; }
  .contact__row svg { width: 7px; height: 7px; fill: var(--white); }
  .contact__web { margin-top: 8px; font-weight: 500; }

  /* Outside: front cover */
  .front-cover {
    background: linear-gradient(160deg, var(--white) 0%, var(--paper) 60%, var(--paper-shade) 100%);
  }
  .wordmark {
    position: absolute;
    left: 0; right: 0;
    top: 185px;
    display: flex;
    justify-content: center;
    align-items: center;
    gap: 12px;
  }
  .wordmark__square {
    width: 26px; height: 26px;
    background: var(--brand-blue);
  }
  .wordmark__text { font-family: "Montserrat", Arial, sans-serif; color: var(--ink); font-weight: 600; }
  .wordmark__name { font-size: 28px; letter-spacing: 4px; line-height: 1; }
  .wordmark__tag { font-size: 7.5px; letter-spacing: 2.6px; margin-top: 4px; }

  .footer-band {
    position: absolute;
    left: 0; right: 0; bottom: 0;
    height: 26px;
  }
  .footer-band__line {
    position: absolute; left: 0; right: 0; bottom: 8px;
    height: 3px; background: var(--ink);
  }
  .footer-band__blue {
    position: absolute; left: 0; right: 0; bottom: 0;
    height: 8px; background: var(--brand-blue);
  }
  .footer-band__tab {
    position: absolute; right: 0; bottom: 8px;
    height: 16px; width: 130px;
    background: var(--brand-blue);
    clip-path: polygon(10px 0, 100% 0, 100% 100%, 0 100%);
    color: var(--white);
    font-size: 8px;
    display: flex; align-items: center; justify-content: flex-end;
    padding-right: 8px;
  }

  /* Inside */
  .inside-panel {
    background: linear-gradient(180deg, var(--white) 0%, var(--paper) 100%);
  }
  .inside-panel + .inside-panel { border-left: 1px solid #dcdcdc; }
  .pocket {
    position: absolute;
    left: 0; right: 0; bottom: 0;
    height: 200px;
    background: linear-gradient(135deg, var(--brand-blue) 0%, var(--brand-blue-light) 60%, var(--brand-blue) 100%);
    box-shadow: 0 -4px 10px rgba(0,0,0,0.12);
  }
  .pocket--left { clip-path: polygon(0 0, 100% 30px, 100% 100%, 0 100%); }
  .pocket--right { clip-path: polygon(0 30px, 100% 0, 100% 100%, 0 100%); }
  .card-slot { position: absolute; background: var(--ink); opacity: 0.8; }
  .card-slot--h { width: 14px; height: 1.5px; }
  .card-slot--v { width: 1.5px; height: 14px; }
</style>
</head>
<body>

<section class="spread spread--outside" aria-label="Folder outside">
  <div class="panel back-cover">
    <div class="contact">
      <div class="contact__address">1420 Birchwood Road<br>Fairbanks, Alaska 99701</div>
      <div class="contact__row"><svg viewBox="0 0 10 10"><path d="M2 0h2l1 3-1.5 1a6 6 0 0 0 2.5 2.5L7 5l3 1v2a2 2 0 0 1-2 2A8 8 0 0 1 0 2a2 2 0 0 1 2-2z"/></svg>555 210 4830</div>
      <div class="contact__row"><svg viewBox="0 0 10 10"><rect x="2" y="0" width="6" height="10" rx="1"/></svg>555 318 7742</div>
      <div class="contact__row"><svg viewBox="0 0 10 10"><rect x="0" y="3" width="10" height="5" rx="1"/><rect x="2" y="0" width="6" height="3"/></svg>555 402 1196</div>
      <div class="contact__row"><svg viewBox="0 0 10 10"><rect x="0" y="2" width="10" height="6"/></svg>dispatch@harlowfreight.com</div>
      <div class="contact__web">www.harlowfreight.com</div>
    </div>
  </div>
  <div class="panel front-cover">
    <div class="wordmark">
      <div class="wordmark__square"></div>
      <div class="wordmark__text">
        <div class="wordmark__name">HARLOW</div>
        <div class="wordmark__tag">FREIGHT · LINES</div>
      </div>
    </div>
    <div class="footer-band">
      <div class="footer-band__line"></div>
      <div class="footer-band__blue"></div>
      <div class="footer-band__tab">www.harlowfreight.com</div>
    </div>
  </div>
</section>

<section class="spread spread--inside" aria-label="Folder inside">
  <div class="panel inside-panel">
    <div class="pocket pocket--left">
      <span class="card-slot card-slot--h" style="left:60px;top:70px"></span>
      <span class="card-slot card-slot--v" style="left:150px;top:100px"></span>
      <span class="card-slot card-slot--h" style="left:60px;top:150px"></span>
    </div>
  </div>
  <div class="panel inside-panel">
    <div class="pocket pocket--right">
      <span class="card-slot card-slot--h" style="left:130px;top:60px"></span>
      <span class="card-slot card-slot--v" style="left:110px;top:110px"></span>
      <span class="card-slot card-slot--v" style="left:250px;top:110px"></span>
      <span class="card-slot card-slot--h" style="left:230px;top:160px"></span>
    </div>
  </div>
</section>

</body>
</html>
```